We want to design total new business card and logo for Kestrel Building Services Ltd

Our company name Kestrel Building Services Ltd. Design new logo and business card , need hi-end luxury style art for architecture and construction industry. The card should simple but stylish. Our business focus on CONNECT tradesman to construction company, help marketing construction company tender oversea projects, managing franchise in construction sector, delivery amazing services to our client, so Logo should show the CONNECTION IDEA, CONNECTING PEOPLE, LUXURY. Visit our website for more information: kestrelgroup.example.nz

Target Market(s)

Directors or managers

Industry/Entity Type

Construction Company

Contact Information for Business Card

Name, Title, Mobile, Email, Website

Font styles to use
Serif

Colors

Designer to choose colors to be used in the design.

Requirements
Must have
• Simple and luxury, connection icon
Nice to have
• Special materials, plastic card, look through,...
• Look new ideas.

```html
<!DOCTYPE html>
<html lang="en">
<head>
<meta charset="utf-8">
<title>Kestrel Building Services – Business Card</title>
<link rel="stylesheet" href="https://fonts.googleapis.com/css2?family=Libre+Baskerville:wght@400;700&family=Poppins:wght@400;500;600;700&display=swap">
<style>
  :root {
    --stage: #e6e8ea;
    --card-white: #ffffff;
    --card-dark: #141618;
    --card-dark-edge: #22272a;
    --accent: #2fb4d8;
    --accent-muted: #4f7c86;
    --ink: #2a2a2a;
    --ink-soft: #3c3c3c;
    --rule: #4a4a4a;
  }
  * { margin: 0; padding: 0; box-sizing: border-box; }
  html, body {
    width: 1200px;
    height: 900px;
    overflow: hidden;
    background: var(--stage);
  }
  .stage {
    position: relative;
    width: 1200px;
    height: 900px;
  }
  .card {
    position: absolute;
    width: 560px;
    height: 320px;
    border-radius: 4px;
    box-shadow: 0 10px 30px rgba(0,0,0,0.18);
    overflow: hidden;
  }
  /* Back face */
  .card-back {
    left: 80px;
    top: 90px;
    background: linear-gradient(135deg, var(--card-dark-edge) 0%, var(--card-dark) 60%);
    display: flex;
    align-items: center;
    justify-content: center;
  }
  .card-back .back-name {
    font-family: "Libre Baskerville", serif;
    font-weight: 400;
    font-size: 22px;
    letter-spacing: 3px;
    text-transform: uppercase;
    color: var(--accent);
  }
  /* Front face */
  .card-front {
    left: 560px;
    top: 490px;
    background: var(--card-white);
  }
  .brand {
    position: absolute;
    left: 24px;
    top: 118px;
    width: 276px;
    display: flex;
    flex-direction: column;
    align-items: center;
    text-align: center;
  }
  .brand-mark {
    width: 34px;
    height: 34px;
    border-radius: 50%;
    background: var(--accent);
    margin-bottom: 10px;
  }
  .brand-name {
    font-family: "Libre Baskerville", serif;
    font-weight: 400;
    font-size: 14px;
    letter-spacing: 0.4px;
    text-transform: uppercase;
    color: var(--ink-soft);
    white-space: nowrap;
  }
  .brand-tagline {
    margin-top: 5px;
    font-family: "Libre Baskerville", serif;
    font-weight: 700;
    font-size: 9px;
    color: var(--accent-muted);
  }
  .divider {
    position: absolute;
    left: 318px;
    top: 58px;
    width: 1px;
    height: 200px;
    background: var(--rule);
  }
  .contact {
    position: absolute;
    left: 336px;
    top: 66px;
    font-family: "Poppins", sans-serif;
  }
  .person-name {
    font-weight: 700;
    font-size: 21px;
    line-height: 1.1;
    color: var(--accent);
    text-transform: uppercase;
  }
  .person-title {
    font-weight: 400;
    font-size: 13px;
    color: var(--ink);
    margin-bottom: 12px;
  }
  .contact-list { list-style: none; }
  .contact-item {
    display: flex;
    align-items: center;
    gap: 9px;
    font-weight: 500;
    font-size: 11.5px;
    line-height: 22px;
    color: var(--ink);
    white-space: nowrap;
  }
  .contact-icon {
    width: 13px;
    height: 13px;
    flex: none;
    fill: var(--accent);
  }
</style>
</head>
<body>
<main class="stage">

  <section class="card card-back" aria-label="Business card back">
    <span class="back-name">Kestrel Building Services</span>
  </section>

  <section class="card card-front" aria-label="Business card front">
    <div class="brand">
      <span class="brand-mark" aria-hidden="true"></span>
      <div class="brand-name">Kestrel Building Services</div>
      <div class="brand-tagline">Amazing services Affordable price</div>
    </div>

    <div class="divider"></div>

    <div class="contact">
      <div class="person-name">Your Name</div>
      <div class="person-title">Your Title</div>
      <ul class="contact-list">
        <li class="contact-item">
          <svg class="contact-icon" viewBox="0 0 24 24"><path d="M6.6 10.8a15.1 15.1 0 0 0 6.6 6.6l2.2-2.2c.3-.3.7-.4 1-.2 1.1.4 2.3.6 3.6.6.6 0 1 .4 1 1V20c0 .6-.4 1-1 1C10.6 21 3 13.4 3 4c0-.6.4-1 1-1h3.5c.6 0 1 .4 1 1 0 1.3.2 2.5.6 3.6.1.3 0 .7-.2 1z"/></svg>
          0800 555 014
        </li>
        <li class="contact-item">
          <svg class="contact-icon" viewBox="0 0 24 24"><path d="M6.6 10.8a15.1 15.1 0 0 0 6.6 6.6l2.2-2.2c.3-.3.7-.4 1-.2 1.1.4 2.3.6 3.6.6.6 0 1 .4 1 1V20c0 .6-.4 1-1 1C10.6 21 3 13.4 3 4c0-.6.4-1 1-1h3.5c.6 0 1 .4 1 1 0 1.3.2 2.5.6 3.6.1.3 0 .7-.2 1z"/></svg>
          021 555 0192
        </li>
        <li class="contact-item">
          <svg class="contact-icon" viewBox="0 0 24 24"><path d="M2 5h20v14H2z M2 5l10 8 10-8" fill="none" stroke="var(--accent)" stroke-width="2.4"/></svg>
          info@kestrelgroup.example.nz
        </li>
        <li class="contact-item">
          <svg class="contact-icon" viewBox="0 0 24 24"><circle cx="12" cy="12" r="10"/><path d="M2 12h20M12 2c3 3 3 17 0 20M12 2c-3 3-3 17 0 20" fill="none" stroke="#fff" stroke-width="1.4"/></svg>
          www.kestrelgroup.example.nz
        </li>
      </ul>
    </div>
  </section>

</main>
</body>
</html>
```